Design my site www.brieflyledger.com

So here is what I am thinking in terms of design:

https://plenvo.com

https://www.skyluxair.com

http://kalvex.com/harbor-plaza-tower/

I want the theme to be white and blue (royal blue). I attached a paint picture of what I would like the site to look like in terms of placing the text. Generally, what I like about the sites above is that they are simple, you can navigate easily and have some kind of idea of what's going on by looking at the center (picture and motto). Let's establish a clear understanding of how the functional part of the site would look like. Please see the picture attached.

I want to keep it simple: On top would be the Name 'BRIEFLY ledger", somewhere to the right on top on the page would be 'Sign in" button.

In the center would be a picture (maybe a video) with the Motto (on top of it all in capital) OBSERVE NAVIGATE DECIDE and below would be the "sign up now"

Below the picture (like on kalvex.com site) or to the left on top of the page would be "About Us', "Press" "Contact Us' buttons.

Then once the user gets to his page his got 3 tabs " Press Headlines", "Events", " Briefings".

we would keep the same format I only have on the site, but separate for every Tab.

I do not want the user to get distracted. I also want him to be able to access the page though mobile phone and be able to get automatic updates just like Zorvan Pings without having to sign in daily.

The landing page must be minimalist yet with business/corporate feel where users can navigate easily and a "what you see is what you get" approach. You want an image or video (personally I prefer the video.. it does capture the users attention instantly, as long as it is an interesting video), with your taglines in it.

Sections available to public: About Us, Contact Us, Landing Page with Signup Option

Private: Public Sections + User Account Page, Tabs for (Events, Press Headlines, Briefings)

Target Market(s)

PR/media monitoring/diplomatic community

Coding

Coded - Design and coding required

Number of Pages Required

1 page

Font styles to use
Serif
Sans Serif

Colors
0255a3
ec1f27

Requirements
Must have
• a simple landing page, that is user friendly.
Nice to have
• a video with the explanation of how to navigate the site
Should not have
• too many colors, graphs etc.

```html
<!DOCTYPE html>
<html lang="en">
<head>
<meta charset="utf-8">
<title>BRIEFLY LEDGER</title>
<link rel="stylesheet" href="https://fonts.googleapis.com/css2?family=Arimo:wght@400;700&family=Open+Sans:wght@400;600;700&display=swap">
<style>
  :root {
    --royal-blue: #0255a3;
    --royal-blue-dark: #0a4a90;
    --accent-red: #ec1f27;
    --white: #ffffff;
    --heading-text: #3a3a3a;
    --meta-text: #333333;
    --body-text: #6f6f6f;
    --footer-top: #4a4a4a;
    --footer-bottom: #2e2e2e;
    --footer-text: #ffffff;
    --sky-light: #d3dcdf;
    --sky-mid: #a9bcc5;
    --city-tone: #8fa3ae;
    --photo-tone-top: #c9c2b8;
    --photo-tone-bottom: #b3a79a;
  }
  * { margin: 0; padding: 0; box-sizing: border-box; }
  html, body { width: 1200px; height: 657px; overflow: hidden; }
  body {
    position: relative;
    font-family: "Open Sans", Arial, sans-serif;
    background: var(--sky-light);
  }
  .hero-backdrop {
    position: absolute; inset: 0;
    background: linear-gradient(180deg, var(--sky-mid) 0%, var(--sky-light) 40%, var(--city-tone) 100%);
  }
  .site-header .brand {
    position: absolute; left: 97px; top: 48px;
    font-family: "Arimo", Arial, sans-serif;
    font-weight: 700; font-size: 31px; letter-spacing: 0.2px;
    color: var(--white);
  }
  .sign-in {
    position: absolute; left: 1017px; top: 50px;
    width: 86px; height: 37px;
    border-radius: 3px;
    background: linear-gradient(180deg, var(--royal-blue) 0%, var(--royal-blue-dark) 100%);
    color: var(--white);
    font-family: "Arimo", Arial, sans-serif; font-size: 16px;
    display: flex; align-items: center; justify-content: center;
  }
  .dashboard {
    position: absolute; left: 150px; top: 147px;
    width: 899px; height: 377px;
    box-shadow: 2px 3px 6px rgba(0,0,0,0.35);
  }
  .tab-bar { display: flex; height: 49px; background: var(--royal-blue); }
  .tab {
    flex: 1; display: flex; align-items: center; justify-content: center;
    font-family: "Arimo", Arial, sans-serif; font-size: 22px;
    color: var(--white); position: relative;
  }
  .tab.is-active { background: var(--accent-red); }
  .tab + .tab + .tab::before {
    content: ""; position: absolute; left: 0; top: 10px; bottom: 8px;
    width: 1px; background: rgba(0,0,0,0.35);
  }
  .tab-panel { position: relative; height: 328px; background: var(--white); }
  .article-photo {
    position: absolute; left: 47px; top: 49px;
    width: 295px; height: 233px;
    border: 1px solid #bdbdbd;
    background: linear-gradient(180deg, var(--photo-tone-top) 0%, var(--photo-tone-bottom) 100%);
  }
  .article-body { position: absolute; left: 365px; top: 61px; width: 350px; }
  .article-title { font-size: 17px; font-weight: 600; color: var(--heading-text); line-height: 24px; }
  .article-meta {
    display: flex; align-items: center; gap: 12px;
    margin-top: 15px; margin-left: 2px;
    font-size: 11px; color: var(--meta-text);
  }
  .meta-item { display: flex; align-items: center; gap: 5px; }
  .meta-item svg { display: block; }
  .article-excerpt {
    margin-top: 13px; margin-left: 2px; width: 344px;
    font-size: 12px; line-height: 19.7px; color: var(--body-text);
    text-align: justify;
  }
  .read-more {
    display: flex; align-items: center; gap: 6px;
    margin-top: 14px; margin-left: 3px;
    font-size: 12px; font-weight: 600; color: var(--royal-blue);
    text-decoration: none;
  }
  .site-footer {
    position: absolute; left: 0; top: 607px; width: 1200px; height: 50px;
    background: linear-gradient(180deg, var(--footer-top) 0%, var(--footer-bottom) 100%);
    color: var(--footer-text); font-size: 12px;
  }
  .copyright { position: absolute; left: 104px; top: 17px; }
  .footer-links { position: absolute; left: 969px; top: 17px; display: flex; gap: 19px; }
  .footer-links a { color: var(--footer-text); text-decoration: none; }
</style>
</head>
<body>
  <div class="hero-backdrop" role="img" aria-label="Background photograph of an office tower and city skyline"></div>

  <header class="site-header">
    <div class="brand">BRIEFLY LEDGER</div>
    <a class="sign-in">SIGN IN</a>
  </header>

  <main class="dashboard">
    <nav class="tab-bar">
      <div class="tab is-active">PRESS HEADLINES</div>
      <div class="tab">EVENTS</div>
      <div class="tab">BRIEFINGS</div>
    </nav>
    <section class="tab-panel">
      <div class="article-photo" role="img" aria-label="Article photograph: a reader with a newspaper"></div>
      <article class="article-body">
        <h2 class="article-title">De Finibus Bonorum et Malorum</h2>
        <div class="article-meta">
          <span class="meta-item">
            <svg width="11" height="11" viewBox="0 0 11 11"><rect x="0.5" y="1.5" width="10" height="9" fill="none" stroke="#ec1f27"/><rect x="0.5" y="1.5" width="10" height="2.5" fill="#ec1f27"/><path d="M3 0v2M8 0v2M2.5 6h2M6.5 6h2M2.5 8.3h2M6.5 8.3h2" stroke="#ec1f27"/></svg>
            May 28th, 2015
          </span>
          <span class="meta-item">
            <svg width="12" height="11" viewBox="0 0 12 11"><path d="M6 1C3 1 1 2.7 1 4.6c0 1.2.8 2.2 2 2.8L2.5 9.8 5 8c.3.1.7.1 1 .1 3 0 5-1.7 5-3.6S9 1 6 1z" fill="none" stroke="#ec1f27" stroke-width="1.1"/></svg>
            0
          </span>
          <span class="meta-item">
            <svg width="13" height="9" viewBox="0 0 13 9"><path d="M0.5 4.5C2 1.8 4 .5 6.5.5s4.5 1.3 6 4c-1.5 2.7-3.5 4-6 4s-4.5-1.3-6-4z" fill="#ec1f27"/><circle cx="6.5" cy="4.5" r="2" fill="#fff"/><circle cx="6.5" cy="4.5" r="1" fill="#ec1f27"/></svg>
            321
          </span>
        </div>
        <p class="article-excerpt">Sed ut perspiciatis unde omnis iste natus error sit voluptatem accusantium doloremque laudantium, totam rem aperiam, eaque ipsa quae ab illo inventore veritatis et quasi architecto beatae vitae dicta sunt explicabo.</p>
        <a class="read-more">READ MORE
          <svg width="12" height="12" viewBox="0 0 12 12"><circle cx="6" cy="6" r="5" fill="none" stroke="#0255a3" stroke-width="1.6"/><path d="M3.5 6h4.5M6 3.8 8.2 6 6 8.2" fill="none" stroke="#0255a3" stroke-width="1.5"/></svg>
        </a>
      </article>
    </section>
  </main>

  <footer class="site-footer">
    <p class="copyright">Copyright © 2016 BRIEFLY ledger</p>
    <nav class="footer-links">
      <a>Terms of Use</a>
      <a>Privacy</a>
    </nav>
  </footer>
</body>
</html>
```